Coach/consultant in conflict and challenge needs an enticing flyer

I need a double sided DL flyer design that will describe my work in helping people meet conflict and emotional challenge so they can learn and grow from these difficulties. I want to give a flavour of my style through fresh colours, repeated images used differently (the spiral), and a sense of positivity around conflict and difficulty. I want to attract people who are keen to do things differently and want to engage with creative processes rather than getting stuck in familiar patterns. My work is creative and often includes use of story, images and fables, so I want to convey that as well. I also place the work in a spiritual context, but grounded in practicality so I don't want it to seem New Age or flakey. I want something that seems innovative, professional and intriguing. I've included a sample of something I mocked up in word and also a copy of a flyer for Merle Tavener's Lantern Passage that inspired me to get a DL flyer. I want the design to communicate trust and transformation and engaging with fresh ways of doing things by moving past old habits

Target Market(s)

Mid 30s plus women and men who want to change their approach to conflict and emotional difficulties and are willing to take the creative and challenging journey to do that

Industry/Entity Type

Learn

Colors
acd136
00a990

Requirements
Must have
• a shift in the use of the spiral image,
• use of image of me (Wynne)
• bright fresh colours olours that represent growth and transformation--I've suggested lime green as it suggests a sense of growth
• easy to read text
Nice to have
• Interesting non-traditional fonts perhaps text in a contemporary sans serif and another brush script font (like the Lantern Passage example)
• bleed to the edge and run off the page images or text
Should not have
• anything that represents too much tradition or stuckness

```html
<!DOCTYPE html>
<html lang="en">
<head>
<meta charset="utf-8">
<title>Wynne Halloway – DL Flyer Colour Proofs</title>
<link rel="stylesheet" href="https://fonts.googleapis.com/css2?family=Nanum+Brush+Script&family=Nanum+Pen+Script&family=Didact+Gothic&family=Mulish:ital,wght@1,700&display=swap">
<style>
  :root {
    --page: #ffffff;
    --label: #111111;
    --white: #ffffff;
    --rgb-field: #97b61f;
    --rgb-field-deep: #8ea61c;
    --rgb-accent: #55e6d8;
    --rgb-ink: #5c6414;
    --cmyk-field: #8fb03a;
    --cmyk-field-deep: #86a037;
    --cmyk-accent: #72cfc9;
    --cmyk-ink: #606a26;
  }
  * { margin: 0; padding: 0; box-sizing: border-box; }
  html, body {
    width: 1066px; height: 1200px; overflow: hidden;
    background: var(--page);
  }
  .sheet { position: relative; width: 1066px; height: 1200px; }

  .proof-label {
    position: absolute; left: 0; width: 1066px;
    font-family: "Helvetica Neue", Helvetica, Arial, sans-serif;
    font-weight: 400; font-size: 36px; line-height: 44px;
    color: var(--label); text-align: center;
  }
  .proof-label--rgb { top: 78px; left: -1px; }
  .proof-label--cmyk { top: 620px; left: -14px; }

  .card {
    --field: var(--rgb-field);
    --field-deep: var(--rgb-field-deep);
    --accent: var(--rgb-accent);
    --ink: var(--rgb-ink);
    position: absolute; left: 125px; width: 747px; height: 392px;
    background: var(--field); overflow: hidden;
  }
  .card--rgb { top: 156px; }
  .card--cmyk {
    top: 684px;
    --field: var(--cmyk-field);
    --field-deep: var(--cmyk-field-deep);
    --accent: var(--cmyk-accent);
    --ink: var(--cmyk-ink);
  }

  .feature-art {
    position: absolute; left: 0; top: 0; width: 280px; height: 392px;
    background: linear-gradient(90deg, var(--field-deep) 0%, var(--field-deep) 55%, var(--field) 100%);
  }

  .card-copy { position: absolute; left: 283px; top: 0; width: 450px; }
  .name {
    position: absolute; top: 36px; left: 0;
    font-family: "Nanum Brush Script", cursive;
    font-weight: 400; font-size: 84px; line-height: 1;
    color: var(--white); white-space: nowrap;
  }
  .values {
    position: absolute; top: 122px; left: 7px; width: 403px;
    display: flex; justify-content: space-between;
    font-family: "Nanum Pen Script", cursive;
    font-size: 32px; line-height: 1; color: var(--accent);
    white-space: nowrap;
  }
  .intro {
    position: absolute; top: 194px; left: 0; width: 428px;
    font-family: "Didact Gothic", sans-serif; font-size: 16.6px;
    line-height: 19.6px; color: var(--white);
  }
  .about {
    position: absolute; top: 297px; left: 2px; width: 440px;
    font-family: "Mulish", sans-serif; font-style: italic; font-weight: 700;
    font-size: 15.6px; line-height: 19.6px; color: var(--ink);
  }
</style>
</head>
<body>
<main class="sheet">
  <h2 class="proof-label proof-label--rgb">RGB Color</h2>
  <section class="card card--rgb">
    <div class="feature-art" role="img" aria-label="Painted turquoise brush spiral over large faint olive spiral strokes"></div>
    <div class="card-copy">
      <h1 class="name">Wynne Halloway</h1>
      <p class="values"><span>#courage</span><span>#listening</span><span>#creativity</span></p>
      <p class="intro">Challenge, change and conflict are a natural part of life. When we greet them with courage, and listen to what they tell us, we grow in wisdom, resilience and creativity.</p>
      <p class="about">Wynne Halloway is a coach, educator and mediator. She works with people who want to harvest the fruits of challenge and conflict so they can live life differently.</p>
    </div>
  </section>

  <h2 class="proof-label proof-label--cmyk">CMYK Color</h2>
  <section class="card card--cmyk">
    <div class="feature-art" role="img" aria-label="Painted turquoise brush spiral over large faint olive spiral strokes"></div>
    <div class="card-copy">
      <h1 class="name">Wynne Halloway</h1>
      <p class="values"><span>#courage</span><span>#listening</span><span>#creativity</span></p>
      <p class="intro">Challenge, change and conflict are a natural part of life. When we greet them with courage, and listen to what they tell us, we grow in wisdom, resilience and creativity.</p>
      <p class="about">Wynne Halloway is a coach, educator and mediator. She works with people who want to harvest the fruits of challenge and conflict so they can live life differently.</p>
    </div>
  </section>
</main>
</body>
</html>
```